Website design for legal tech start up in Switzerland (B2B)

We are for a legal tech start up in Switzerland called KOVA. We have been running since August 2016. This will be our first live website.

We need a website designed and business card design for our start-up in Switzerland. We also need the Web design to be converted into HTML and CSS files.

Function of website:
• To inform potential customers of our services
• Form a key part of our digital marketing and sales footprint.
• Branding

Please find attached logo.
Updates

Project Deadline Extended Reason: Giving us time to review submissions and provide opportunity for more submissions. Added Thursday, February 16, 2017

Project Deadline Extended
Reason: Looking for more idea's not necessarily set on blue and grey colours only.

Target Market(s)

B2B tech powered legal services.

Industry/Entity Type

Legal

Contact Information for Business Card

Lean and slick design.

Coding

Coded - Design and coding required

Number of Pages Required

5+ page

Requirements
Must have
• VERY LEAN AND CLEAN DESIGN!
• We have received many great standard designs, but we are looking for something more out-of-the box: You can get inspiration from these designs: http://www.pixelvane.com/websites/clean/
• Thanks!!
• Easy content management system
• Well structured coding for additional development
• Responsive webpage for all types of devices
• SEO optimized
• Tabs (Home, services, team, careers, blog, contact us)
• Colour scheme complementary to logo
Nice to have
• Look and Design - Approachable, High-tech, Modern
• Easy to add chat bot capability in future
Should not have
• Too busy/ too much clutter
• Not take to long to load

```html
<!DOCTYPE html>
<html lang="en">
<head>
<meta charset="utf-8">
<title>KOVA – Legal Tech Services</title>
<link href="https://fonts.googleapis.com/css2?family=Lato:wght@300;400;700;900&display=swap" rel="stylesheet">
<style>
:root{
  --navy:#1d3c6e;
  --navy-dark:#14294d;
  --ink:#2f3237;
  --charcoal:#3b3e44;
  --grey:#7b7f86;
  --light:#eef0f3;
  --line:#cfd3d9;
  --white:#ffffff;
  --footer:#12151c;
}
*{box-sizing:border-box;margin:0;padding:0}
html,body{width:1200px;height:3448px;overflow:hidden}
body{font-family:"Lato",sans-serif;color:var(--ink);background:var(--white)}
section,header,footer{position:relative;width:1200px;overflow:hidden}
.abs{position:absolute}

/* header */
.site-header{height:115px;background:var(--white)}
.brand{left:80px;top:20px;font-size:72px;font-weight:900;letter-spacing:4px;color:var(--charcoal);line-height:1}
.top-phone{right:85px;top:24px;display:flex;align-items:center;gap:8px;font-size:22px;color:var(--navy)}
.top-phone .dot{width:32px;height:32px;border-radius:50%;background:var(--navy-dark);display:flex;align-items:center;justify-content:center}
.main-nav{right:85px;top:76px;display:flex;gap:34px;font-size:16px;letter-spacing:.5px}
.main-nav a{color:var(--ink);text-decoration:none;padding-bottom:10px}
.main-nav a.active{color:var(--navy);font-weight:700;border-bottom:3px solid var(--navy)}
.nav-mark{left:586px;top:44px;color:#9aa0a8;font-size:26px;font-weight:300}

/* hero */
.hero{height:533px;background:linear-gradient(90deg,#1b2230 0%,#2a3446 40%,#3f5f8f 62%,#7b8fb3 80%,#b7a6b8 100%)}
.hero-photo{inset:0;background:linear-gradient(180deg,rgba(20,30,50,.1) 0%,rgba(10,14,22,.55) 100%)}
.hero-title{left:85px;top:205px;color:var(--white);font-size:43px;font-weight:400;line-height:56px;letter-spacing:1px}
.btn-outline{left:80px;top:453px;width:316px;height:64px;border:2px solid var(--white);background:var(--navy-dark);color:var(--white);font-size:20px;display:flex;align-items:center;justify-content:center;letter-spacing:.5px}

/* about */
.about{height:410px;background:linear-gradient(180deg,#f4f5f7,#e9ebef)}
.section-heading{font-size:40px;font-weight:400;color:var(--ink);letter-spacing:1px}
.about .section-heading{left:80px;top:68px}
.about .section-heading b{color:var(--navy);font-weight:900}
.about-rule{left:80px;top:120px;width:255px;height:2px;background:var(--navy)}
.about-copy{left:80px;top:144px;width:650px;font-size:13px;line-height:24px;color:#444}
.pillar{top:280px;display:flex;gap:14px}
.pillar .badge{width:78px;height:78px;border-radius:50%;border:4px solid var(--navy);background:var(--white);display:flex;align-items:center;justify-content:center}
.pillar h4{font-size:18px;font-weight:400;margin-top:4px}
.pillar p{font-size:11.5px;line-height:15px;color:#666;width:180px;margin-top:4px}
.quick-form{left:752px;top:65px;width:352px;height:300px;background:var(--white);box-shadow:0 2px 8px rgba(0,0,0,.12)}
.quick-form .tab{position:absolute;left:20px;top:-10px;width:310px;height:48px;background:var(--navy-dark);color:var(--white);text-align:center;padding-top:6px}
.quick-form .tab strong{display:block;font-size:16px;font-weight:400;letter-spacing:.5px}
.quick-form .tab span{font-size:11px}
.field{position:absolute;left:20px;width:312px;height:34px;border:1px solid var(--line);font-size:12px;color:#888;padding:9px 10px}
.field em{color:#c33;font-style:normal}
.submit{position:absolute;left:20px;top:238px;width:108px;height:34px;background:var(--navy-dark);color:var(--white);font-size:15px;font-weight:700;display:flex;align-items:center;justify-content:center;letter-spacing:1px}

/* services */
.services{height:662px;background:var(--white)}
.center-heading{left:0;width:1200px;text-align:center}
.divider{left:330px;width:540px;height:20px}
.service-card{width:330px;height:234px;background:var(--white);box-shadow:0 2px 5px rgba(0,0,0,.15)}
.service-card .photo{height:177px}
.service-card .icon{position:absolute;left:142px;top:150px;width:46px;height:46px;border-radius:50%;background:var(--white);display:flex;align-items:center;justify-content:center}
.service-card .label{position:absolute;left:0;right:0;top:200px;text-align:center;font-size:17px;color:var(--ink)}
.service-card .label.active{color:var(--navy)}
.service-card.first .label{border-bottom:3px solid var(--navy);padding-bottom:8px}

/* cta band */
.cta-band{height:87px;background:var(--navy-dark);color:var(--white)}
.cta-band .ask{left:80px;top:26px;font-size:29px;letter-spacing:.5px}
.cta-band .offer{left:430px;top:22px;display:flex;align-items:center;gap:14px;font-size:22px}
.round-ico{width:46px;height:46px;border-radius:50%;background:#3d4350;display:flex;align-items:center;justify-content:center}
.cta-band .or{left:800px;top:31px;font-size:18px;color:#6b7b98}
.cta-band .call{left:855px;top:20px;display:flex;align-items:center;gap:14px}
.cta-band .call small{display:block;font-size:12px;color:#aab4c8}
.cta-band .call strong{font-size:28px;font-weight:400}

/* why */
.why{height:584px;background:linear-gradient(180deg,#ffffff,#f0f1f4)}
.why .center-heading b{color:var(--navy);font-weight:900}
.reason{width:260px;text-align:center}
.reason h5{font-size:18px;font-weight:700;color:var(--ink)}
.reason p{font-size:13px;line-height:18px;color:#666;margin-top:4px}
.reason .go{width:22px;height:22px;border-radius:50%;margin:10px auto 0;display:flex;align-items:center;justify-content:center}
.reason.top .go{background:var(--charcoal)}
.reason.bottom .go{background:var(--navy-dark)}

/* blog */
.blog{height:575px;background:var(--white)}
.post{width:330px;height:345px;background:var(--white);box-shadow:0 2px 6px rgba(0,0,0,.15)}
.post .photo{height:188px}
.post .date{position:absolute;left:16px;top:210px;width:36px;background:var(--navy-dark);color:var(--white);text-align:center;font-size:13px;line-height:17px;padding:3px 0}
.post .date small{display:block;background:#e8eaee;color:var(--ink);font-size:8px;line-height:12px}
.post h6{position:absolute;left:68px;top:210px;font-size:13px;font-weight:400;color:var(--ink)}
.post .meta{position:absolute;left:68px;top:238px;font-size:12px;color:#777}
.post .meta b{color:var(--ink);font-weight:400}
.post .excerpt{position:absolute;left:68px;top:268px;width:240px;font-size:12px;line-height:20px;color:#888}
.pager{left:586px;top:546px;display:flex;gap:8px}
.pager i{width:10px;height:10px;border-radius:50%;border:1px solid #999;display:block}
.pager i.on{background:var(--navy-dark);border-color:var(--navy-dark)}

/* footer */
.site-footer{height:482px;background:linear-gradient(180deg,#1a2130 0%,#0f131b 100%);color:var(--white)}
.contact-col{width:320px;text-align:center;font-size:12px}
.contact-col svg{display:block;margin:0 auto 16px}
.foot-brand{left:0;width:1200px;top:158px;text-align:center;font-size:54px;font-weight:900;letter-spacing:6px}
.foot-copy{left:300px;width:600px;top:222px;text-align:center;font-size:12.5px;line-height:20px;color:#d3d6dc}
.hours{left:0;width:1200px;top:288px;display:flex;justify-content:center;gap:20px}
.hours span{background:#2b3140;padding:5px 14px;font-size:12px}
.foot-btn{left:540px;top:346px;width:120px;height:32px;border:1px solid var(--white);font-size:13px;display:flex;align-items:center;justify-content:center}
.foot-rule{left:80px;width:1040px;top:410px;height:1px;background:rgba(255,255,255,.2)}
.copyright{left:80px;top:436px;font-size:12px;color:#c9ccd2}
.social{right:80px;top:424px;display:flex;gap:12px}
.social i{width:38px;height:38px;border-radius:50%;display:block;background:var(--navy)}
.social i:nth-child(2){background:#1f5f9e}
.social i:nth-child(3){background:#2f8fd0}
.social i:nth-child(4){background:#c8462f}
</style>
</head>
<body>

<header class="site-header">
  <div class="abs brand">KOVA</div>
  <div class="abs nav-mark">×</div>
  <div class="abs top-phone">
    <span class="dot"><svg width="16" height="16" viewBox="0 0 24 24"><path fill="#fff" d="M6.6 10.8a15 15 0 0 0 6.6 6.6l2.2-2.2c.3-.3.7-.4 1-.2 1.1.4 2.3.6 3.6.6.6 0 1 .4 1 1V20c0 .6-.4 1-1 1A17 17 0 0 1 3 4c0-.6.4-1 1-1h3.5c.6 0 1 .4 1 1 0 1.3.2 2.5.6 3.6.1.3 0 .7-.2 1z"/></svg></span>
    +41 22 555 0148
  </div>
  <nav class="abs main-nav">
    <a class="active">HOME</a><a>SERVICES</a><a>TEAM</a><a>CAREERS</a><a>BLOG</a><a>CONTACT US</a>
  </nav>
</header>

<section class="hero">
  <div class="abs hero-photo" role="img" aria-label="City skyline with glass office towers at dusk"></div>
  <h1 class="abs hero-title">WE ARE EXPERT IN<br>LEGAL ADVISOR</h1>
  <div class="abs btn-outline">GET A FREE CONSULTATION</div>
</section>

<section class="about">
  <h2 class="abs section-heading">ABOUT <b>KOVA</b></h2>
  <div class="abs about-rule"></div>
  <p class="abs about-copy">eaque ipsa quae ab illo inventore veritatis et quasi architecto beatae vitae dicta sunt explicabo. Sed ut perspiciatis unde omnis iste natus error sit voluptatem accusantium dolore remque laudantium, totam rem aperiam, eaque ipsa quae ab illo inventore veritatis et quasi architecto beatae vitae dicta sunt explicabo. Sed ut perspiciatis unde omnis iste natus error sit voluptatem accusantium dolo eaque ipsa quae ab illo inventore veritatis et quasi architecto beatae vitae dicta sunt explicabo.</p>
  <div class="abs pillar" style="left:85px">
    <div class="badge"><svg width="40" height="40" viewBox="0 0 40 40"><circle cx="20" cy="20" r="18" fill="#1d3c6e"/><circle cx="14" cy="16" r="4" fill="#fff"/><circle cx="26" cy="16" r="4" fill="#fff"/><path d="M7 29a7 7 0 0 1 14 0zM19 29a7 7 0 0 1 14 0z" fill="#fff"/></svg></div>
    <div><h4>Our Misshion</h4><p>Sed ut perspiciatis unde omnis iste natus error sit voluptatem accusantium.</p></div>
  </div>
  <div class="abs pillar" style="left:378px">
    <div class="badge"><svg width="40" height="40" viewBox="0 0 40 40"><circle cx="20" cy="20" r="16" fill="none" stroke="#1d3c6e" stroke-width="4"/><circle cx="20" cy="20" r="9" fill="none" stroke="#1d3c6e" stroke-width="4"/><circle cx="20" cy="20" r="3" fill="#1d3c6e"/><path d="M20 20L34 6" stroke="#2f3237" stroke-width="3"/></svg></div>
    <div><h4>Our Vision</h4><p>Sed ut perspiciatis unde omnis iste natus error sit voluptatem accusantium.</p></div>
  </div>
  <form class="abs quick-form">
    <div class="tab"><strong>QUICK CONTACT WITH US</strong><span>Get a FREE Consultation</span></div>
    <div class="field" style="top:52px">Name <em>*</em></div>
    <div class="field" style="top:98px">Email <em>*</em></div>
    <div class="field" style="top:144px">Phone <em>*</em></div>
    <div class="field" style="top:190px">Select Services<em>*</em><span style="float:right;color:#555">⌄</span></div>
    <div class="submit">SUBMIT &nbsp;»</div>
  </form>
</section>

<section class="services">
  <h2 class="abs section-heading center-heading" style="top:22px">OUR <b style="color:var(--navy);font-weight:900">SERVICES</b></h2>
  <svg class="abs divider" style="top:70px" viewBox="0 0 540 20"><line x1="0" y1="10" x2="255" y2="10" stroke="#c9ccd2"/><line x1="285" y1="10" x2="540" y2="10" stroke="#c9ccd2"/><path d="M264 4l12 12M276 4L264 16" stroke="#9aa0a8" stroke-width="2"/></svg>

  <div class="abs service-card first" style="left:80px;top:122px">
    <div class="photo" role="img" aria-label="Hands working on a tablet showing business charts" style="background:linear-gradient(135deg,#cdd8e6,#6f8db5)"></div>
    <div class="icon"><svg width="24" height="24"><rect x="4" y="12" width="4" height="8" fill="#1d3c6e"/><rect x="10" y="7" width="4" height="13" fill="#1d3c6e"/><rect x="16" y="4" width="4" height="16" fill="#1d3c6e"/></svg></div>
    <div class="label active">Information Management</div>
  </div>
  <div class="abs service-card" style="left:436px;top:122px">
    <div class="photo" role="img" aria-label="Consultant on the phone at a desk with laptop" style="background:linear-gradient(135deg,#e6ecf2,#8fa3bc)"></div>
    <div class="icon"><svg width="24" height="24"><circle cx="12" cy="8" r="5" fill="#2f3237"/><path d="M3 22a9 9 0 0 1 18 0z" fill="#2f3237"/></svg></div>
    <div class="label">Case Support</div>
  </div>
  <div class="abs service-card" style="left:791px;top:122px">
    <div class="photo" role="img" aria-label="Hand touching a digital interface of app screens" style="background:linear-gradient(135deg,#1d2a44,#4b6a9a)"></div>
    <div class="icon"><svg width="24" height="24"><rect x="3" y="4" width="18" height="13" rx="2" fill="#2f3237"/><rect x="9" y="18" width="6" height="3" fill="#2f3237"/></svg></div>
    <div class="label">Application Development</div>
  </div>
  <div class="abs service-card" style="left:80px;top:389px">
    <div class="photo" role="img" aria-label="Looking up into a green forest canopy" style="background:linear-gradient(135deg,#a9c97a,#3f6b2d)"></div>
    <div class="icon"><svg width="24" height="24"><path d="M12 2l7 12H5z" fill="#2f3237"/><rect x="11" y="14" width="2" height="7" fill="#2f3237"/></svg></div>
    <div class="label">Environmental Litigation</div>
  </div>
  <div class="abs service-card" style="left:436px;top:389px">
    <div class="photo" role="img" aria-label="Person writing in a book on a wooden desk" style="background:linear-gradient(135deg,#5a3a28,#c7a27c)"></div>
    <div class="icon"><svg width="24" height="24"><circle cx="12" cy="12" r="9" fill="none" stroke="#2f3237" stroke-width="4" stroke-dasharray="4 3"/><circle cx="12" cy="12" r="3" fill="#2f3237"/></svg></div>
    <div class="label">Legal Word Processing</div>
  </div>
  <div class="abs service-card" style="left:791px;top:389px">
    <div class="photo" role="img" aria-label="Hand holding a ball bearing over technical drawings" style="background:linear-gradient(135deg,#dfe2e6,#8d939b)"></div>
    <div class="icon"><svg width="24" height="24"><rect x="9" y="3" width="6" height="5" fill="#2f3237"/><rect x="2" y="16" width="6" height="5" fill="#2f3237"/><rect x="16" y="16" width="6" height="5" fill="#2f3237"/><path d="M12 8v4M5 16v-4h14v4" stroke="#2f3237" stroke-width="2" fill="none"/></svg></div>
    <div class="label">Procurement Support</div>
  </div>
</section>

<section class="cta-band">
  <div class="abs ask">NEED A LEGAL ADVICE &nbsp;?</div>
  <div class="abs offer"><span class="round-ico"><svg width="22" height="22"><circle cx="11" cy="7" r="5" fill="#fff"/><path d="M2 21a9 9 0 0 1 18 0z" fill="#fff"/></svg></span>Get A FREE CONSULTATION</div>
  <div class="abs or">OR</div>
  <div class="abs call"><span class="round-ico"><svg width="20" height="20" viewBox="0 0 24 24"><path fill="#fff" d="M6.6 10.8a15 15 0 0 0 6.6 6.6l2.2-2.2c.3-.3.7-.4 1-.2 1.1.4 2.3.6 3.6.6.6 0 1 .4 1 1V20c0 .6-.4 1-1 1A17 17 0 0 1 3 4c0-.6.4-1 1-1h3.5c.6 0 1 .4 1 1 0 1.3.2 2.5.6 3.6.1.3 0 .7-.2 1z"/></svg></span><div><small>Call Us Today</small><strong>+41 22 555 0148</strong></div></div>
</section>

<section class="why">
  <h2 class="abs section-heading center-heading" style="top:28px">WHY <b>CHOOSE US ?</b></h2>
  <svg class="abs divider" style="top:83px" viewBox="0 0 540 20"><line x1="0" y1="10" x2="255" y2="10" stroke="#c9ccd2"/><line x1="285" y1="10" x2="540" y2="10" stroke="#c9ccd2"/><path d="M264 4l12 12M276 4L264 16" stroke="#9aa0a8" stroke-width="2"/></svg>

  <div class="abs reason top" style="left:40px;top:143px"><h5 style="text-align:left;padding-left:48px">Strategic Planning</h5><p>Duis autem vel eum iriure do in hendrerit in vulputate.</p><div class="go"><svg width="8" height="10"><path d="M1 1l5 4-5 4" stroke="#fff" stroke-width="2" fill="none"/></svg></div></div>
  <div class="abs reason top" style="left:387px;top:143px"><h5>Creative</h5><p>Duis autem vel eum iriure do in hendrerit in vulputate.</p><div class="go"><svg width="8" height="10"><path d="M1 1l5 4-5 4" stroke="#fff" stroke-width="2" fill="none"/></svg></div></div>
  <div class="abs reason top" style="left:721px;top:143px"><h5>Consulting Practice</h5><p>Duis autem vel eum iriure do in hendrerit in vulputate.</p><div class="go"><svg width="8" height="10"><path d="M1 1l5 4-5 4" stroke="#fff" stroke-width="2" fill="none"/></svg></div></div>

  <svg class="abs" style="left:80px;top:235px" width="1040" height="190" viewBox="0 0 1040 190">
    <path d="M0 110 H20 A82 82 0 0 0 184 110 H20" fill="none"/>
    <path d="M0 95 A0 0 0 0 0 0 95" />
    <!-- lower dark arcs -->
    <path d="M20 110 A82 82 0 0 0 184 110 L150 110 A48 48 0 0 1 54 110 Z" fill="#3b3e44"/>
    <path d="M355 110 A82 82 0 0 0 519 110 L485 110 A48 48 0 0 1 389 110 Z" fill="#3b3e44"/>
    <path d="M689 110 A82 82 0 0 0 853 110 L819 110 A48 48 0 0 1 723 110 Z" fill="#3b3e44"/>
    <!-- upper navy arcs -->
    <path d="M183 110 A82 82 0 0 1 347 110 L313 110 A48 48 0 0 0 217 110 Z" fill="#1d3c6e"/>
    <path d="M519 110 A82 82 0 0 1 683 110 L649 110 A48 48 0 0 0 553 110 Z" fill="#1d3c6e"/>
    <path d="M854 110 A82 82 0 0 1 1018 110 L1040 110 L984 110 A48 48 0 0 0 888 110 Z" fill="#1d3c6e"/>
    <path d="M0 110 H20 V128 H0Z" fill="#3b3e44"/>
    <g fill="#fff" stroke="#e2e4e8" stroke-width="2">
      <circle cx="102" cy="110" r="50"/><circle cx="265" cy="110" r="50"/><circle cx="437" cy="110" r="50"/>
      <circle cx="601" cy="110" r="50"/><circle cx="771" cy="110" r="50"/><circle cx="936" cy="110" r="50"/>
    </g>
    <g fill="#2f3237">
      <path d="M84 94h14v8a5 5 0 1 1 0 10v8H84z"/><path d="M102 112h14v14h-14z" fill="#1d3c6e"/>
      <rect x="245" y="92" width="38" height="28" fill="none" stroke="#2f3237" stroke-width="3"/><rect x="252" y="106" width="4" height="10"/><rect x="259" y="100" width="4" height="16"/><circle cx="280" cy="120" r="7" fill="none" stroke="#2f3237" stroke-width="3"/><path d="M285 125l6 6" stroke="#2f3237" stroke-width="3"/>
      <path d="M437 90a14 14 0 0 1 8 25v6h-16v-6a14 14 0 0 1 8-25z"/><rect x="431" y="124" width="12" height="4"/>
      <rect x="584" y="112" width="7" height="14"/><rect x="595" y="104" width="7" height="22"/><rect x="606" y="96" width="7" height="30"/><path d="M582 106l14-10 8 6 14-12" stroke="#1d3c6e" stroke-width="3" fill="none"/>
      <rect x="753" y="90" width="36" height="22" rx="2" fill="none" stroke="#2f3237" stroke-width="3"/><circle cx="760" cy="118" r="5"/><circle cx="782" cy="118" r="5"/><path d="M750 132a10 10 0 0 1 20 0zM772 132a10 10 0 0 1 20 0z"/>
      <path d="M918 92h30a6 6 0 0 1 6 6v16a6 6 0 0 1-6 6h-18l-10 8v-8h-2a6 6 0 0 1-6-6V98a6 6 0 0 1 6-6z" fill="none" stroke="#2f3237" stroke-width="3"/><circle cx="925" cy="106" r="2.5"/><circle cx="933" cy="106" r="2.5"/><circle cx="941" cy="106" r="2.5"/>
    </g>
  </svg>

  <div class="abs reason bottom" style="left:205px;top:434px"><h5>Market Research</h5><p>Duis autem vel eum iriure do in hendrerit in vulputate.</p><div class="go"><svg width="8" height="10"><path d="M1 1l5 4-5 4" stroke="#fff" stroke-width="2" fill="none"/></svg></div></div>
  <div class="abs reason bottom" style="left:557px;top:434px"><h5>High Value</h5><p>Duis autem vel eum iriure do in hendrerit in vulputate.</p><div class="go"><svg width="8" height="10"><path d="M1 1l5 4-5 4" stroke="#fff" stroke-width="2" fill="none"/></svg></div></div>
  <div class="abs reason bottom" style="left:886px;top:434px"><h5>Translate</h5><p>Duis autem vel eum iriure do in hendrerit in vulputate.</p><div class="go"><svg width="8" height="10"><path d="M1 1l5 4-5 4" stroke="#fff" stroke-width="2" fill="none"/></svg></div></div>
</section>

<section class="blog">
  <h2 class="abs section-heading center-heading" style="top:46px">LATEST <b style="color:var(--navy);font-weight:900">BLOG</b></h2>
  <svg class="abs divider" style="top:100px" viewBox="0 0 540 20"><line x1="0" y1="10" x2="255" y2="10" stroke="#c9ccd2"/><line x1="285" y1="10" x2="540" y2="10" stroke="#c9ccd2"/><path d="M264 4l12 12M276 4L264 16" stroke="#9aa0a8" stroke-width="2"/></svg>

  <article class="abs post" style="left:80px;top:162px">
    <div class="photo" role="img" aria-label="Hand touching a glowing blue circuit network" style="background:linear-gradient(135deg,#0f2a55,#3d7fc4)"></div>
    <div class="date">24<small>APR</small></div>
    <h6>Lorem ipsum dolor sit amet,</h6>
    <div class="meta">by <b>admin</b> &nbsp;| &nbsp;in news, business</div>
    <p class="excerpt">Ut wisi enim ad minim veniam, quis nostrud exerci tation ullamcorper.</p>
  </article>
  <article class="abs post" style="left:436px;top:162px">
    <div class="photo" role="img" aria-label="Business team joining puzzle pieces seen from below" style="background:linear-gradient(135deg,#c9d6e6,#5e7491)"></div>
    <div class="date">24<small>APR</small></div>
    <h6>Duis autem vel eum iriure dolo,</h6>
    <div class="meta">by <b>admin</b> &nbsp;| &nbsp;in news, business</div>
    <p class="excerpt">Ut wisi enim ad minim veniam, quis nostrud exerci tation ullamcorper.</p>
  </article>
  <article class="abs post" style="left:791px;top:162px">
    <div class="photo" role="img" aria-label="Desk with newspaper, calculator, coffee and documents" style="background:linear-gradient(135deg,#e7ddcf,#8b6d52)"></div>
    <div class="date">24<small>APR</small></div>
    <h6>Vel illum dolore eu feugiat nulla</h6>
    <div class="meta">by <b>admin</b> &nbsp;| &nbsp;in news, business</div>
    <p class="excerpt">Ut wisi enim ad minim veniam, quis nostrud exerci tation ullamcorper.</p>
  </article>
  <div class="abs pager"><i class="on"></i><i></i></div>
</section>

<footer class="site-footer" role="img" aria-label="Night city skyline behind dark overlay">
  <div class="abs contact-col" style="left:139px;top:48px"><svg width="24" height="30" viewBox="0 0 24 30"><path d="M12 2a9 9 0 0 1 9 9c0 7-9 17-9 17S3 18 3 11a9 9 0 0 1 9-9z" fill="none" stroke="#aab0ba" stroke-width="2"/><circle cx="12" cy="11" r="3" fill="none" stroke="#aab0ba" stroke-width="2"/></svg>12 Lorem ipsum dolor 456 Sed diam, nonummy</div>
  <div class="abs contact-col" style="left:440px;top:48px"><svg width="28" height="30" viewBox="0 0 24 24"><path fill="none" stroke="#aab0ba" stroke-width="1.6" d="M6.6 10.8a15 15 0 0 0 6.6 6.6l2.2-2.2c.3-.3.7-.4 1-.2 1.1.4 2.3.6 3.6.6.6 0 1 .4 1 1V20c0 .6-.4 1-1 1A17 17 0 0 1 3 4c0-.6.4-1 1-1h3.5c.6 0 1 .4 1 1 0 1.3.2 2.5.6 3.6.1.3 0 .7-.2 1z"/></svg>Phone: +41 22 555 0149</div>
  <div class="abs contact-col" style="left:748px;top:48px"><svg width="30" height="30" viewBox="0 0 30 30"><path d="M3 14L27 3 20 27l-6-9z M14 18l13-15" fill="none" stroke="#aab0ba" stroke-width="2"/></svg>Email: info@kova.ch</div>
  <div class="abs foot-brand">KOVA</div>
  <p class="abs foot-copy">Lorem ipsum dolor sit amet, consectetuer adipiscing elit, sed diam nonummy nibh euismod tincidunt ut laoreet dolore magna aliquam</p>
  <div class="abs hours"><span>MON - FRI: 8:00 - 17:00</span><span>SATURDAY: 9:00 - 15:00</span><span>SUNDAY: CLOSED</span></div>
  <div class="abs foot-btn">CONTACT US</div>
  <div class="abs foot-rule"></div>
  <div class="abs copyright">Copyright © 2016 KOVA . All Right Reserved.</div>
  <div class="abs social"><i></i><i></i><i></i><i></i></div>
</footer>

</body>
</html>
```